MEDICAL CLINIC LETTERHEAD

Design is a letterhead for a non-profit medical center. The name of the clinic is VITARIDGE Community Health Center. Although the full name must be included, the community health center part is more of a description and should be less visible - i attached an example of what I mean by that (ATTACHED IMAGE IS AN EXAMPLE OF FONT SIZES NOT A DESIGN IDEA). Please design something modern, cool looking and unique because I can always download free templates.
Phone, email, website and etc will be added later.

Industry/Entity Type

MEDICAL

```html
<!DOCTYPE html>
<html lang="en">
<head>
<meta charset="utf-8">
<title>VITARIDGE Community Health Center – Letterhead</title>
<link rel="stylesheet" href="https://fonts.googleapis.com/css2?family=Questrial&family=Montserrat:wght@500;700&family=Open+Sans:wght@600&display=swap">
<style>
  :root {
    --navy: #1c2b4d;
    --gold: #a8874f;
    --ink-soft: #9a9a9c;
    --ink-mid: #8c8c8e;
    --paper: #ffffff;
    --sig-fill: #f1f1f3;
  }
  * { margin: 0; padding: 0; box-sizing: border-box; }
  html, body { width: 908px; height: 1200px; overflow: hidden; background: var(--paper); }
  .letterhead {
    position: relative; width: 908px; height: 1200px;
    background: var(--paper); font-family: "Questrial", sans-serif; color: var(--ink-soft);
  }
  .brand { position: absolute; left: 34px; top: 62px; color: var(--navy); font-family: "Questrial", sans-serif; }
  .brand-name { font-size: 34px; letter-spacing: 0.5px; line-height: 1; }
  .brand-descriptor { font-size: 8px; letter-spacing: 0.6px; margin-top: 4px; }

  .sender { position: absolute; left: 41px; top: 278px; }
  .sender-name {
    font-family: "Montserrat", sans-serif; font-weight: 700; font-size: 27px;
    color: var(--ink-mid); letter-spacing: 0.5px; margin-bottom: 10px;
  }
  .sender-line { font-family: "Montserrat", sans-serif; font-weight: 500; font-size: 14px; color: var(--ink-soft); line-height: 1.5; margin-bottom: 8px; }
  .sender-address { line-height: 21px; }

  .letter-date {
    position: absolute; right: 43px; top: 540px;
    font-family: "Open Sans", sans-serif; font-weight: 600; font-size: 17px; color: var(--ink-mid);
  }

  .letter-body { position: absolute; left: 36px; width: 829px; font-size: 16px; line-height: 20px; text-align: justify; color: var(--ink-soft); }
  .letter-body p { margin-bottom: 0; }
  .body-one { top: 452px; }
  .body-two { top: 595px; }
  .body-three { top: 734px; }

  .signoff-title { position: absolute; left: 66px; top: 848px; font-size: 22px; color: var(--ink-mid); }
  .signature { position: absolute; left: 86px; top: 905px; width: 172px; height: 105px; border-radius: 4px; background: var(--sig-fill); }

  .contact-list { position: absolute; left: 39px; top: 1078px; list-style: none; }
  .contact-item { display: flex; align-items: center; height: 29px; font-size: 18px; color: var(--ink-mid); }
  .contact-icon { width: 16px; height: 16px; margin-right: 6px; flex: none; }
</style>
</head>
<body>
<main class="letterhead">
  <header class="brand">
    <div class="brand-name">VITARIDGE</div>
    <div class="brand-descriptor">COMMUNITY HEALTH CENTER</div>
  </header>

  <section class="sender">
    <h1 class="sender-name">DANA WHITFIELD</h1>
    <p class="sender-line">0198-765-432</p>
    <p class="sender-line">info@harborlinemail.com</p>
    <p class="sender-line sender-address">5678 Maple Grove Ln. Suite<br>45 Austin, TX 0000</p>
  </section>

  <p class="letter-date">12 December, 2023</p>

  <div class="letter-body body-one">
    <p>Lorem ipsum dolor sit amet, consectetuer adipiscing elit, sed diam nonummy nibh euismod tincidunt ut laoreet dolore magna aliquam erat volutpat. Ut wisi enim ad minim veniam, quis nostrud exerci tation ullamcorper suscipit lobortis nisl ut aliquip ex ea commodo consequat. Duis autem vel eum iriure dolor in hendrerit in vulputate velit esse molestie consequat, vel illum dolore eu feugiat nulla facilisis at vero eros et accumsan et iusto odio dignissim qui blandit praesent luptatum zzril delenit augue duis dolore te feugait nulla facilisi.</p>
  </div>
  <div class="letter-body body-two">
    <p>Lorem ipsum dolor sit amet, cons ectetuer adipiscing elit, sed diam nonummy nibh euismod tincidunt ut laoreet dolore magna aliquam erat volutpat. Ut wisi enim ad minim veniam, quis nostrud exerci tation ullamcorper suscipit lobortis nisl ut aliquip ex ea commodo consequat.</p>
    <p>Lorem ipsum dolor sit amet, consectetuer adipiscing elit, sed diam nonummy nibh euismod tincidunt ut laoreet dolore magna aliquam erat</p>
  </div>
  <div class="letter-body body-three">
    <p>Lorem ipsum dolor sit amet, cons ectetuer adipiscing elit, sed diam nonummy nibh euismod tincidunt ut laoreet dolore magna aliquam erat volutpat. Ut wisi enim ad minim veniam, quis nostrud exerci tation ullamcorper suscipit lobortis nisl ut aliquip ex ea commodo consequat. Lorem ipsum dolor sit zamet, consectetuer adipiscing elit, sed diam nonummy nibh euismod tincidunt.</p>
  </div>

  <p class="signoff-title">Managing Director</p>
  <div class="signature" role="img" aria-label="Handwritten signature of the managing director"></div>

  <ul class="contact-list">
    <li class="contact-item">
      <svg class="contact-icon" viewBox="0 0 16 16" aria-hidden="true"><circle cx="8" cy="8" r="8" fill="var(--navy)"/><path d="M5.2 4.2l1.4-.3.8 1.8-.9.8c.5 1 1.3 1.8 2.3 2.3l.8-.9 1.8.8-.3 1.4c-3.3.2-6.1-2.6-5.9-5.9z" fill="#fff"/></svg>
      <span>0198-765-432</span>
    </li>
    <li class="contact-item">
      <svg class="contact-icon" viewBox="0 0 16 16" aria-hidden="true"><circle cx="8" cy="8" r="8" fill="var(--navy)"/><rect x="4" y="5.2" width="8" height="5.6" rx=".6" fill="#fff"/><path d="M4.3 5.5L8 8.4l3.7-2.9" stroke="var(--navy)" stroke-width=".9" fill="none"/></svg>
      <span>info@vitaridge.com</span>
    </li>
    <li class="contact-item">
      <svg class="contact-icon" viewBox="0 0 16 16" aria-hidden="true"><circle cx="8" cy="8" r="8" fill="var(--navy)"/><g stroke="#fff" stroke-width=".8" fill="none"><circle cx="8" cy="8" r="4.3"/><ellipse cx="8" cy="8" rx="1.8" ry="4.3"/><path d="M3.7 8h8.6M4.3 5.9h7.4M4.3 10.1h7.4"/></g></svg>
      <span>www.vitaridge.com</span>
    </li>
  </ul>
</main>
</body>
</html>
```